Harborview Optical -Window Poster (Optometrist)

We are an optometry practice and we need a poster for a new store promotion for our window highlighting we now also sell 2 pairs of glasses as a package deal. The size will be 1300mm width x 1900mm height

The artwork will be displayed as a fabric banner in our shop window. We have 7 other banners with different services our business provides. The words needs to standout for passers by and the cars stopped at the traffic lights out front of our business. We already have signs with our logos phone number etc. so we won't need them included in the poster.

It would need to include the following information.

Two pair packages now available*

*Conditions apply

The artwork will be displayed as a fabric banner in our shop window. We have 7 other banners with different services our business provides. The words needs to standout for passers by and the cars stopped at the traffic lights out front of our business. We already have signs with our logos phone number etc. so we won't need them included in the poster. Thank you for your work it's amazing Added Saturday, February 18, 2017

The artwork will be displayed as a fabric banner in our shop window. We have 7 other banners with different services our business provides. The words needs to standout for passers by and the cars stopped at the traffic lights out front of our business. We already have signs with our logos phone number etc. so we won't need them included in the poster. Added Saturday, February 18, 2017

Target Market(s)

Cars driving past and stopped at traffic lights outside our store.

Industry/Entity Type

Optician

Requirements
Must have
• Poster must say:
• Two pair packages now available*
• *Conditions apply

```html
<!DOCTYPE html>
<html lang="en">
<head>
<meta charset="utf-8">
<title>Harborview Optical – Two Pair Packages Window Poster</title>
<link rel="stylesheet" href="https://fonts.googleapis.com/css2?family=Roboto+Condensed:wght@700&family=Londrina+Solid:wght@900&display=swap">
<style>
  :root {
    --sky-top: #23317f;
    --sky-mid: #2f55b8;
    --sky-light: #6d93d6;
    --wood-light: #a8916c;
    --wood-dark: #6b5a42;
    --retina: #d94a3a;
    --retina-deep: #b8322a;
    --band: #0b0a1f;
    --white: #ffffff;
    --ink: #0c0c18;
    --yellow: #f2ea1c;
    --orange: #e8922a;
    --frame-red: #b3272b;
    --steel: #4a4f57;
  }
  * { margin: 0; padding: 0; box-sizing: border-box; }
  html, body {
    width: 962px; height: 1200px; overflow: hidden;
    background: #d9d9d9;
  }
  .poster {
    position: relative;
    width: 962px; height: 1200px;
    overflow: hidden;
  }
  .sky {
    position: absolute; inset: 0;
    background: linear-gradient(180deg, var(--sky-top) 0%, var(--sky-mid) 35%, var(--sky-light) 75%, var(--sky-mid) 100%);
  }
  .plank {
    position: absolute; left: 0; width: 962px;
    background: linear-gradient(180deg, var(--wood-light), var(--wood-dark));
  }
  .plank--upper { top: 268px; height: 520px; }
  .plank--lower { top: 901px; height: 299px; }
  .retina {
    position: absolute; left: 46px; top: 136px;
    width: 840px; height: 668px; border-radius: 50%;
    background: radial-gradient(circle at 45% 50%, var(--retina) 0%, var(--retina-deep) 100%);
  }
  .headline-kicker {
    position: absolute; top: 62px; left: 0; width: 100%;
    text-align: center;
    font-family: "Roboto Condensed", sans-serif; font-weight: 700;
    font-size: 58px; letter-spacing: 1px; line-height: 1;
  }
  .headline-kicker .now { color: var(--ink); margin-right: 18px; }
  .headline-kicker .available { color: var(--yellow); }
  .headline-kicker .asterisk { color: var(--yellow); vertical-align: 18px; font-size: 62px; }
  .band {
    position: absolute; left: 25px; width: 918px; height: 192px;
    background: var(--band);
    display: flex; align-items: center; justify-content: center;
    font-family: "Londrina Solid", sans-serif; font-weight: 900;
    font-size: 160px; line-height: 1; letter-spacing: 4px;
    -webkit-text-stroke: 6px #1a1a1a;
    paint-order: stroke fill;
  }
  .band--top { top: 230px; color: var(--white); }
  .band--bottom { top: 602px; color: var(--orange); font-size: 150px; }
  .glasses {
    position: absolute; left: 198px; top: 830px;
    width: 575px; height: 142px; border-radius: 70px;
    background: linear-gradient(180deg, var(--frame-red), #7f1a1e);
  }
  .conditions {
    position: absolute; left: 123px; top: 1022px;
    width: 749px; height: 78px;
    border: 3px solid var(--ink);
    display: flex; align-items: center; justify-content: center;
    font-family: "Roboto Condensed", sans-serif; font-weight: 700;
    font-size: 46px; letter-spacing: 2px; color: var(--ink);
  }
  .bolt {
    position: absolute; width: 88px; height: 88px; border-radius: 50%;
    background: radial-gradient(circle at 40% 35%, #c9ccd2 0%, var(--steel) 60%, #1d1f23 100%);
  }
  .bolt--left { left: 158px; top: 1124px; }
  .bolt--right { left: 760px; top: 1128px; }
</style>
</head>
<body>
  <main class="poster">
    <div class="sky" role="img" aria-label="Blue sky with soft white clouds"></div>
    <div class="plank plank--upper" role="img" aria-label="Weathered wooden plank texture"></div>
    <div class="plank plank--lower" role="img" aria-label="Weathered wooden plank texture"></div>
    <div class="retina" role="img" aria-label="Photograph of a retina, red with fine blood vessels"></div>

    <p class="headline-kicker"><span class="now">NOW</span><span class="available">AVAILABLE</span><span class="asterisk">*</span></p>

    <h1 class="band band--top">TWO PAIR</h1>
    <h2 class="band band--bottom">PACKAGES</h2>

    <div class="glasses" role="img" aria-label="Red framed eyeglasses resting on the wooden plank"></div>

    <p class="conditions">*CONDITIONS APPLY</p>

    <div class="bolt bolt--left" role="img" aria-label="Round metal bolt head"></div>
    <div class="bolt bolt--right" role="img" aria-label="Round metal bolt head"></div>
  </main>
</body>
</html>
```